Brickfield real estate investment company needs a poster design

We would like a poster design size 18 x 24.
Poster wording -
I WANT TO BUY YOUR ( finish with logo) logo uploaded
website- www.brickfield.example
phone # 555-218-7043 ( color red for the phone number)
we would like to see the poster on 2 different backgrounds
Yellow background
White background
horizontal

```html
<!DOCTYPE html>
<html lang="en">
<head>
<meta charset="utf-8">
<title>Brickfield — I Want To Buy Your Home Poster</title>
<link rel="stylesheet" href="https://fonts.googleapis.com/css2?family=Montserrat:wght@400;500;800&display=swap">
<style>
  :root {
    --backdrop: #e9e9e7;
    --poster-yellow: #ffdf17;
    --ink: #111111;
    --accent-red: #e8232f;
    --shadow: rgba(0, 0, 0, 0.18);
  }
  * { margin: 0; padding: 0; box-sizing: border-box; }
  html, body {
    width: 1200px;
    height: 1200px;
    overflow: hidden;
    background: var(--backdrop);
  }
  .poster {
    position: absolute;
    left: 0;
    top: 137px;
    width: 1200px;
    height: 926px;
    background: var(--poster-yellow);
    box-shadow: 0 6px 18px var(--shadow);
    font-family: "Montserrat", Arial, sans-serif;
    color: var(--ink);
    text-align: center;
  }
  .poster__line {
    position: absolute;
    left: 0;
    right: 0;
    line-height: 1;
  }
  .headline {
    top: 192px;
    font-size: 76px;
    font-weight: 500;
    letter-spacing: 1px;
  }
  .headline__emphasis {
    color: var(--accent-red);
    font-weight: 800;
  }
  .brand-name {
    top: 410px;
    font-size: 132px;
    font-weight: 800;
    letter-spacing: -2px;
    color: var(--ink);
  }
  .phone {
    top: 692px;
    font-size: 92px;
    font-weight: 800;
    color: var(--accent-red);
    letter-spacing: 0;
  }
  .website {
    top: 818px;
    font-size: 40px;
    font-weight: 400;
    letter-spacing: 3px;
  }
</style>
</head>
<body>
  <main class="poster">
    <h1 class="poster__line headline">I WANT TO <span class="headline__emphasis">BUY</span> YOUR</h1>
    <p class="poster__line brand-name">Brickfield</p>
    <p class="poster__line phone">555-218-7043</p>
    <p class="poster__line website">www.brickfield.example</p>
  </main>
</body>
</html>
```